World Wide News and Current Affairs website

We intends to start up a new website which deals on New and Current Affairs.
Attention Designers,
We want a home page design for this project. Our business is based in the United States. Our goal is to become a well known brand.
The website would consist of a category for News, Business and Tech.
The theme should be beautiful and attention seeking. The website would take bulk of it's news from the US, and Europe.
Designers can get inspiration from already existing new websites such as PWJ, KLV, DASKOLM.
All designs should be clean and easy to navigate.

```html
<!DOCTYPE html>
<html lang="en">
<head>
<meta charset="utf-8">
<title>Harlow News</title>
<link href="https://fonts.googleapis.com/css2?family=Open+Sans:wght@400;600;700&display=swap" rel="stylesheet">
<style>
:root{
  --orange:#f7931e;
  --dark:#2e2e2e;
  --darker:#262626;
  --text:#333333;
  --muted:#777777;
  --line:#e4e4e4;
  --white:#ffffff;
}
*{box-sizing:border-box;margin:0;padding:0}
html,body{width:1200px;height:2731px;overflow:hidden}
body{position:relative;font-family:"Open Sans",Arial,sans-serif;color:var(--text);background:var(--white);font-size:12px}
.abs{position:absolute}
.photo{position:absolute;border-radius:0}

/* header */
.site-header{position:absolute;left:0;top:0;width:1200px;height:64px;background:var(--dark);border-bottom:4px solid var(--orange)}
.brand{position:absolute;left:131px;top:17px;font-size:23px;font-weight:700;color:var(--orange);letter-spacing:.3px;white-space:nowrap}
.main-nav a{position:absolute;top:23px;color:var(--white);text-decoration:none;font-size:11.5px;white-space:nowrap}
.search{position:absolute;left:909px;top:19px;width:158px;height:26px;background:var(--white);border:1px solid #ccc;font-size:10.5px;color:#999;padding:5px 8px}
.search svg{position:absolute;right:7px;top:7px}

/* hero */
.hero-img{left:131px;top:80px;width:936px;height:332px;background:linear-gradient(135deg,#6f6a62 0%,#a39886 35%,#8b7a63 55%,#d2d0cc 80%,#9aa0a4 100%)}
.hero-arrow{position:absolute;top:371px;width:38px;height:33px;background:var(--orange)}
.hero-band{position:absolute;left:131px;top:412px;width:936px;height:92px;background:rgba(40,40,40,.93)}
.hero-band h2{position:absolute;left:12px;top:13px;color:var(--white);font-size:18px;font-weight:700}
.hero-band p{position:absolute;left:12px;top:44px;width:815px;color:#eee;font-size:10.8px;line-height:21px}
.cta{position:absolute;right:0;top:0;width:104px;height:92px;background:var(--orange);color:var(--white);font-weight:700;font-size:13px;display:flex;align-items:center;justify-content:center}

/* section headings */
.sec-head{position:absolute;height:36px;border-bottom:3px solid var(--orange)}
.sec-head span{display:inline-block;height:33px;background:var(--dark);color:var(--white);font-weight:600;font-size:15.5px;line-height:33px;padding:0 20px}

.panel{position:absolute;border:1px solid var(--line);background:var(--white)}

.orange{color:var(--orange)}
.title{font-weight:600;font-size:13.5px;color:var(--text);line-height:22px}
.body{font-size:11.5px;color:var(--muted);line-height:21px}
.meta{font-size:11px;display:flex;align-items:center;gap:6px}

/* news list */
.side-item{position:absolute;left:690px;width:377px}
.side-item p{font-size:12px;line-height:23px;width:235px}
.side-item .meta{margin-top:8px}
.sep{position:absolute;left:690px;width:361px;height:1px;background:var(--line)}

.cat-list{position:absolute;left:806px;top:1127px;list-style:none}
.cat-list li{height:30px;font-size:11px;color:var(--muted);display:flex;align-items:center;gap:12px}
.cat-list svg{flex:none}

.btn{position:absolute;width:80px;height:29px;background:var(--orange);color:var(--white);font-size:12px;display:flex;align-items:center;justify-content:center}

.recent{position:absolute;left:801px;width:260px}
.recent p{position:absolute;left:94px;top:0;width:160px;font-size:11.5px;line-height:22px}
.recent .meta{position:absolute;left:94px;top:52px;font-size:10px}

/* videos */
.videos{position:absolute;left:0;top:2049px;width:1200px;height:340px;background:var(--dark);border-bottom:5px solid var(--orange)}
.videos h2{position:absolute;left:0;width:1200px;top:50px;text-align:center;color:var(--white);font-size:21px;font-weight:600}
.vid{position:absolute;top:105px;width:220px}
.vid .thumb{height:133px;position:relative}
.vid .play{position:absolute;left:10px;bottom:8px;display:flex;align-items:center;gap:8px;color:var(--white);font-size:12px}
.vid p{color:var(--white);font-weight:700;font-size:12.5px;line-height:20px;margin-top:12px}

/* footer */
.foot-col{position:absolute;top:2428px}
.foot-col h3{font-size:13px;font-weight:600;color:var(--text);margin-bottom:10px}
.foot-col ul{list-style:none}
.foot-col li{font-size:11.5px;color:var(--text);height:24px;display:flex;align-items:center;gap:9px}
.foot-col li::before{content:"›";color:#888;font-size:13px}
.email{position:absolute;left:841px;top:2460px;width:226px;height:35px;border:1px solid var(--line);font-size:10px;color:#aaa;padding:10px 14px}
.subscribe{position:absolute;left:841px;top:2504px;width:90px;height:35px;background:var(--orange);color:var(--white);font-weight:700;font-size:12px;display:flex;align-items:center;justify-content:center}
.social{position:absolute;left:841px;top:2599px;display:flex;gap:6px}
.social span{width:27px;height:27px;border-radius:50%}
.copyright{position:absolute;left:0;top:2681px;width:1200px;height:50px;background:#f4f4f4;text-align:center;font-size:11.5px;line-height:50px;color:var(--text)}
</style>
</head>
<body>

<header class="site-header">
  <div class="brand">HARLOW NEWS</div>
  <nav class="main-nav">
    <a style="left:399px">Home</a><a style="left:459px">Business</a><a style="left:533px">Markets</a><a style="left:606px">Politics</a><a style="left:670px">Tech</a><a style="left:723px">Commentary</a><a style="left:821px">Contact</a>
  </nav>
  <div class="search">Search
    <svg width="12" height="12" viewBox="0 0 12 12"><circle cx="5" cy="5" r="3.6" fill="none" stroke="#666" stroke-width="1.4"/><line x1="7.6" y1="7.6" x2="11" y2="11" stroke="#666" stroke-width="1.4"/></svg>
  </div>
</header>

<!-- hero -->
<div class="photo hero-img" role="img" aria-label="Overhead view of a team working around a wooden meeting table with laptops and papers"></div>
<div class="hero-arrow" style="left:131px"><svg width="38" height="33"><polyline points="21,11 16,16.5 21,22" fill="none" stroke="#fff" stroke-width="1.6"/></svg></div>
<div class="hero-arrow" style="left:171px"><svg width="38" height="33"><polyline points="17,11 22,16.5 17,22" fill="none" stroke="#fff" stroke-width="1.6"/></svg></div>
<div class="hero-band">
  <h2>HARLOW NEWS</h2>
  <p>It is a long established fact that a reader will be distracted by the readable content of a page when looking at its layout. The point of using Lorem Ipsum is that it has a more-or-less normal distribution of letters, as opposed to look like readable English</p>
  <div class="cta">CLICK HERE</div>
</div>

<!-- news and current affairs -->
<div class="sec-head" style="left:131px;top:540px;width:936px"><span>NEW AND CURRENT AFFAIRS</span></div>
<div class="panel" style="left:131px;top:594px;width:936px;height:430px"></div>
<div class="photo" style="left:147px;top:615px;width:501px;height:272px;background:linear-gradient(120deg,#cfd6d8 0%,#8a9297 40%,#3b3f44 60%,#b9c48a 85%,#e3e6e6 100%)" role="img" aria-label="Business people in suits meeting in a bright office, video thumbnail"></div>
<svg class="abs" style="left:364px;top:717px" width="68" height="68" viewBox="0 0 68 68"><circle cx="34" cy="34" r="33" fill="#1e1e1e" fill-opacity=".85" stroke="#fff" stroke-width="2"/><polygon points="27,20 50,34 27,48" fill="#fff"/></svg>
<div class="abs title" style="left:153px;top:895px;width:490px">Eiusmod tempor incididunt ut labore et dolore magna aliqua</div>
<div class="abs body" style="left:153px;top:921px;width:480px;line-height:17px;font-size:11px">Accusantium doloremque laudantium, totam rem aperiam, eaque ipsa quae ab illo inven-tore veritatis et quasi architecto beatae vitae Nemo enim ipsam voluptatem quia voluptas sit aspernatur aut odit aut fugit...</div>
<div class="abs meta orange" style="left:153px;top:990px"><svg width="10" height="10"><circle cx="5" cy="5" r="4" fill="none" stroke="#f7931e" stroke-width="1.5"/><polyline points="5,2.5 5,5 6.8,6" fill="none" stroke="#f7931e" stroke-width="1"/></svg>MARCH 29,2017</div>

<div class="side-item" style="top:627px"><p>It is a long established fact that a reader by the readable occaecat...</p><div class="meta"><svg width="10" height="10"><circle cx="5" cy="5" r="4" fill="none" stroke="#f7931e" stroke-width="1.5"/></svg><span class="orange">MARCH 29,2017</span>&nbsp;&nbsp;<span>US &amp; CANADA</span></div></div>
<div class="photo" style="left:932px;top:623px;width:119px;height:96px;background:linear-gradient(135deg,#0c2a3c,#1f6a8a 50%,#0b1c28)" role="img" aria-label="Close-up of a glowing circuit board"></div>
<div class="sep" style="top:737px"></div>
<div class="side-item" style="top:763px"><p>It is a long established fact that a reader by the readable occaecat...</p><div class="meta"><svg width="10" height="10"><circle cx="5" cy="5" r="4" fill="none" stroke="#f7931e" stroke-width="1.5"/></svg><span class="orange">MARCH 29,2017</span>&nbsp;&nbsp;<span>US &amp; CANADA</span></div></div>
<div class="photo" style="left:932px;top:759px;width:119px;height:96px;background:linear-gradient(135deg,#3a3530,#8c6a4a 50%,#c0442f)" role="img" aria-label="Technician working on electronic equipment"></div>
<div class="sep" style="top:874px"></div>
<div class="side-item" style="top:898px"><p>It is a long established fact that a reader by the readable occaecat...</p><div class="meta"><svg width="10" height="10"><circle cx="5" cy="5" r="4" fill="none" stroke="#f7931e" stroke-width="1.5"/></svg><span class="orange">MARCH 29,2017</span>&nbsp;&nbsp;<span>US &amp; CANADA</span></div></div>
<div class="photo" style="left:932px;top:894px;width:119px;height:96px;background:linear-gradient(135deg,#f2f2f2,#d8c2ad 50%,#37475c)" role="img" aria-label="Portrait of a smiling businesswoman"></div>

<!-- tech -->
<div class="sec-head" style="left:131px;top:1061px;width:612px"><span>TECH</span></div>
<div class="photo" style="left:131px;top:1113px;width:295px;height:191px;background:radial-gradient(circle at 50% 50%,#5b6f80 0%,#2a3a47 45%,#11181f 100%)" role="img" aria-label="Hand touching a circular digital interface of app icons"></div>
<div class="photo" style="left:448px;top:1113px;width:295px;height:191px;background:linear-gradient(135deg,#2f4e68,#7f9bb3 50%,#c8d7e2)" role="img" aria-label="Person working with a tablet and charts at a desk"></div>
<div class="abs title" style="left:131px;top:1320px;width:295px">It is a long established fact that a reader will be distracted cupidatat...</div>
<div class="abs title" style="left:448px;top:1320px;width:295px">It is a long established fact that a reader will be distracted cupidatat...</div>
<div class="abs meta" style="left:131px;top:1376px;width:295px"><span class="orange">Jhon SMith</span> - <span class="orange">▦ November 28, 2015</span><svg style="margin-left:auto" width="14" height="13"><rect x="1" y="1" width="12" height="9" fill="none" stroke="#f7931e"/><polyline points="4,10 4,12.5 7,10" fill="none" stroke="#f7931e"/></svg></div>
<div class="abs meta" style="left:448px;top:1376px;width:295px"><span class="orange">Jhon SMith</span> - <span class="orange">▦ November 28, 2015</span><svg style="margin-left:auto" width="14" height="13"><rect x="1" y="1" width="12" height="9" fill="none" stroke="#f7931e"/><polyline points="4,10 4,12.5 7,10" fill="none" stroke="#f7931e"/></svg></div>
<div class="abs body" style="left:131px;top:1404px;width:295px;line-height:23px">It is a long established fact that a reader will tracted by the readable content of a page when looking at its layout. The like readable English...</div>
<div class="abs body" style="left:448px;top:1404px;width:295px;line-height:23px">It is a long established fact that a reader will tracted by the readable content of a page when looking at its layout. The like readable English...</div>

<!-- category -->
<div class="sec-head" style="left:790px;top:1061px;width:277px"><span>CATEGORY</span></div>
<div class="panel" style="left:790px;top:1111px;width:277px;height:237px"></div>
<ul class="cat-list">
  <li><svg width="16" height="16"><circle cx="8" cy="8" r="7" fill="none" stroke="#bbb"/><polyline points="7,5 10,8 7,11" fill="none" stroke="#999"/></svg>Colit is a long voluptatem established ( 4 )</li>
  <li><svg width="16" height="16"><circle cx="8" cy="8" r="7" fill="none" stroke="#bbb"/><polyline points="7,5 10,8 7,11" fill="none" stroke="#999"/></svg>It is a long labore established ( 5 )</li>
  <li><svg width="16" height="16"><circle cx="8" cy="8" r="7" fill="none" stroke="#bbb"/><polyline points="7,5 10,8 7,11" fill="none" stroke="#999"/></svg>Lorem Ipsum proident Dummy ( 30 )</li>
  <li><svg width="16" height="16"><circle cx="8" cy="8" r="7" fill="none" stroke="#bbb"/><polyline points="7,5 10,8 7,11" fill="none" stroke="#999"/></svg>It is a long established ( 41 )</li>
  <li><svg width="16" height="16"><circle cx="8" cy="8" r="7" fill="none" stroke="#bbb"/><polyline points="7,5 10,8 7,11" fill="none" stroke="#999"/></svg>Lorem tempora incidunt Dummy ( 7 )</li>
  <li><svg width="16" height="16"><circle cx="8" cy="8" r="7" fill="none" stroke="#bbb"/><polyline points="7,5 10,8 7,11" fill="none" stroke="#999"/></svg>It is a long established occaecat (23)</li>
  <li><svg width="16" height="16"><circle cx="8" cy="8" r="7" fill="none" stroke="#bbb"/><polyline points="7,5 10,8 7,11" fill="none" stroke="#999"/></svg>It is a long established ( 41 )</li>
</ul>
<div class="photo" style="left:790px;top:1362px;width:277px;height:104px;background:linear-gradient(180deg,#6f8fa8 0%,#51677a 55%,#2a3640 100%)" role="img" aria-label="City skyline of tall office towers"></div>
<div class="abs" style="left:790px;top:1436px;width:277px;height:30px;background:rgba(30,30,30,.55)"></div>
<div class="abs" style="left:804px;top:1442px;color:#fff;font-weight:600;font-size:12.5px">Consectetur Adipiscing</div>
<div class="abs" style="left:1003px;top:1445px;color:#fff;font-size:10px">View More ›</div>

<!-- business news -->
<div class="sec-head" style="left:131px;top:1514px;width:612px"><span>BUSINESS NEWS</span></div>
<div class="abs title" style="left:131px;top:1568px">It is a long established fact that a reader will be distracted cupidatat...</div>
<div class="abs meta" style="left:131px;top:1597px"><span>♟</span><span class="orange">Posted by admin</span>&nbsp;&nbsp;<span>▦</span><span class="orange">May 23, 2015</span>&nbsp;&nbsp;&nbsp;&nbsp;<span>▢</span><span class="orange">4 Comments</span>&nbsp;&nbsp;&nbsp;&nbsp;<span>♡</span><span class="orange">13</span></div>
<div class="photo" style="left:131px;top:1635px;width:210px;height:135px;background:linear-gradient(135deg,#e9edf0,#8d9aa6 45%,#2d2f33 75%,#cfd4d8)" role="img" aria-label="Confident businesswoman standing in front of her team"></div>
<div class="abs body" style="left:366px;top:1636px;width:370px;line-height:23px;color:#555">It is a long established fact that a reader will be distracted by theable content of a page when looking at its layout. The point of using Lorem are Ipsum is that it has a more-or-less normal distribution of letters, as opposed to usingmaking it look like readable English.</div>
<div class="btn" style="left:366px;top:1741px">Read More</div>

<div class="abs title" style="left:131px;top:1803px">It is a long established fact that a reader will be distracted cupidatat...</div>
<div class="abs meta" style="left:131px;top:1833px"><span>♟</span><span class="orange">Posted by admin</span>&nbsp;&nbsp;<span>▦</span><span class="orange">May 23, 2015</span>&nbsp;&nbsp;&nbsp;&nbsp;<span>▢</span><span class="orange">4 Comments</span>&nbsp;&nbsp;&nbsp;&nbsp;<span>♡</span><span class="orange">13</span></div>
<div class="photo" style="left:131px;top:1870px;width:210px;height:135px;background:linear-gradient(135deg,#3c4148,#858c93 45%,#bfc4c8 70%,#50565c)" role="img" aria-label="Two businessmen walking out of a glass office building"></div>
<div class="abs body" style="left:366px;top:1871px;width:370px;line-height:23px;color:#555">It is a long established fact that a reader will be distracted by theable content of a page when looking at its layout. The point of using Lorem are Ipsum is that it has a more-or-less normal distribution of letters, as opposed to usingmaking it look like readable English.</div>
<div class="btn" style="left:366px;top:1976px">Read More</div>

<!-- recent news -->
<div class="sec-head" style="left:790px;top:1514px;width:277px"><span>RECENT NEWS</span></div>
<div class="panel" style="left:790px;top:1562px;width:277px;height:445px"></div>
<div class="recent" style="top:1586px"><div class="photo" style="left:0;top:4px;width:80px;height:72px;background:linear-gradient(135deg,#d9d9d9,#7e7e7e 50%,#3a3a3a)" role="img" aria-label="Stack of newspapers"></div><p>It is a long established fact by the readable...</p><div class="meta"><span>▦</span><span class="orange">FEB 03, 2017</span>&nbsp;<span>▢</span><span class="orange">4 Comments</span></div></div>
<div class="abs" style="left:801px;top:1678px;width:255px;height:1px;background:var(--line)"></div>
<div class="recent" style="top:1690px"><div class="photo" style="left:0;top:4px;width:80px;height:72px;background:linear-gradient(180deg,#2a3f78,#5a6fa8 50%,#d89a4a)" role="img" aria-label="Illuminated building at dusk"></div><p>It is a long established fact by the readable...</p><div class="meta"><span>▦</span><span class="orange">FEB 03, 2017</span>&nbsp;<span>▢</span><span class="orange">4 Comments</span></div></div>
<div class="abs" style="left:801px;top:1782px;width:255px;height:1px;background:var(--line)"></div>
<div class="recent" style="top:1794px"><div class="photo" style="left:0;top:4px;width:80px;height:72px;background:linear-gradient(135deg,#e8ecef,#8fa0b2 50%,#2f4258)" role="img" aria-label="Businessman in a shirt and tie at the office"></div><p>It is a long established fact by the readable...</p><div class="meta"><span>▦</span><span class="orange">FEB 03, 2017</span>&nbsp;<span>▢</span><span class="orange">4 Comments</span></div></div>
<div class="abs" style="left:801px;top:1886px;width:255px;height:1px;background:var(--line)"></div>
<div class="recent" style="top:1905px"><div class="photo" style="left:0;top:4px;width:80px;height:72px;background:linear-gradient(135deg,#c9b9a6,#6d6258 50%,#2c3a4a)" role="img" aria-label="Colleagues shaking hands"></div><p>It is a long established fact by the readable...</p><div class="meta"><span>▦</span><span class="orange">FEB 03, 2017</span>&nbsp;<span>▢</span><span class="orange">4 Comments</span></div></div>

<!-- videos -->
<section class="videos">
  <h2>WATCH VIDEOS</h2>
  <div class="vid" style="left:131px"><div class="thumb photo" style="position:relative;background:linear-gradient(135deg,#d5d8da,#7c858c 50%,#3b4148)" role="img" aria-label="Two colleagues discussing work at a desk"><div class="play"><svg width="20" height="20"><circle cx="10" cy="10" r="9" fill="#222"/><polygon points="8,6 14,10 8,14" fill="#fff"/></svg>2:34</div></div><p>Ratione voluptatem sequi nesc tempora incidunt</p></div>
  <div class="vid" style="left:370px"><div class="thumb photo" style="position:relative;background:linear-gradient(180deg,#0d1420,#2c3446 55%,#b58a4a)" role="img" aria-label="Office building lit up at night"><div class="play"><svg width="20" height="20"><circle cx="10" cy="10" r="9" fill="#222"/><polygon points="8,6 14,10 8,14" fill="#fff"/></svg>2:34</div></div><p>Ratione voluptatem sequi nesc tempora incidunt</p></div>
  <div class="vid" style="left:609px"><div class="thumb photo" style="position:relative;background:linear-gradient(135deg,#e7e3de,#9fa8ae 50%,#4d5660)" role="img" aria-label="Smiling team in a meeting room"><div class="play"><svg width="20" height="20"><circle cx="10" cy="10" r="9" fill="#222"/><polygon points="8,6 14,10 8,14" fill="#fff"/></svg>2:34</div></div><p>Ratione voluptatem sequi nesc tempora incidunt</p></div>
  <div class="vid" style="left:848px"><div class="thumb photo" style="position:relative;background:linear-gradient(135deg,#c8cfd6,#7b8a99 45%,#9b6a4a)" role="img" aria-label="Hands typing on a laptop next to coffee"><div class="play"><svg width="20" height="20"><circle cx="10" cy="10" r="9" fill="#222"/><polygon points="8,6 14,10 8,14" fill="#fff"/></svg>2:34</div></div><p>Ratione voluptatem sequi nesc tempora incidunt</p></div>
</section>

<!-- footer -->
<div class="foot-col" style="left:133px"><h3>OTHER LINKS</h3><ul><li>News</li><li>Sport</li><li>Weather</li><li>Shop</li><li>Earth</li><li>Travel</li></ul></div>
<div class="foot-col" style="left:320px"><h3>TECH</h3><ul><li>Business</li><li>Culture</li><li>Gadgets</li><li>Future</li><li>Startups</li></ul></div>
<div class="foot-col" style="left:488px"><h3>SPORTS</h3><ul><li>Football</li><li>Golf</li><li>Tennis</li><li>Motorsport</li><li>Horseracing</li><li>Equestrian</li><li>Sailing</li><li>Skiing</li></ul></div>
<div class="foot-col" style="left:677px"><h3>MONEY</h3><ul><li>Business</li><li>Markets</li><li>Tech</li></ul><h3 style="margin-top:16px">MEDIA</h3><ul><li>Stars</li><li>Screen</li><li>Video</li></ul></div>
<div class="foot-col" style="left:841px"><h3>NEWSLETTER</h3></div>
<div class="email">Enter Email Address</div>
<div class="subscribe">SUBSCRIBE</div>
<div class="foot-col" style="left:841px;top:2565px"><h3>FOLLOW US</h3></div>
<div class="social" aria-label="Social links">
  <span style="background:#3b5998"></span><span style="background:#0e76a8"></span><span style="background:#f7931e"></span><span style="background:#3cb4e6"></span><span style="background:#d9302a"></span>
</div>

<footer class="copyright">Copyrights © . 2017 | All rights reserved.</footer>

</body>
</html>
```